Design a modern, classy & professional business card for an online real estate agency, specializing in medium-luxury properties in Thailand and later in Singapore and UK.

Possible design ideas so far: (not essential)

- curved corner(s) to the card, white on front & turquoise on back or visa versa.

- front of card - clear and simple, company name in metallic grey/monochrome, logo graphic & company name on front in spot UV or embossed/debossed effect.

- back of card - large, close-cropped, 'ghost' patterns of the C-shaped curves of logo, or company name repeated on back of card in spot UV.

Target Market(s)

- young to middle-aged professionals mainly (but ideally should design should suit all)

- UK, US,EU,AUS & ASIAN mainly (but ideally should design should suit all countries)

Industry/Entity Type

Real Estate

Requirements
Must have
• THEME:
- Luxurious & Modern
- Clean & striking
- Unique & creative

INFO:
- Logo & company name on front
- Contact details on back:

Tobias Hennlund
Managing Director

www.velmontestates.asia
www.velmontestates.co.uk

Tel: 083-274-6159
email: tobias@velmontestates.asia

(contact details can be displayed in any order as suites design.)

Nice to have
• - curved corner(s) to the card, white on front & turquoise on back or visa versa.

Should not have
• - No generic images of properties, palm trees/coconut trees etc.

- No other other bold colors, except for main turquoise, grey, metallic white & black theme.

- No obvious business card templates

```html
<!DOCTYPE html>
<html lang="en">
<head>
<meta charset="utf-8">
<title>Velmont Estates – Business Card</title>
<link rel="stylesheet" href="https://fonts.googleapis.com/css2?family=Exo+2:wght@400;600&display=swap">
<style>
  :root {
    --backdrop: #e6e6e4;
    --card: #ffffff;
    --card-shade: #f1f1f1;
    --band: #8a8a8a;
    --ink: #2f2f2f;
    --ink-soft: #6e6e6e;
    --teal: #2cc6bd;
  }
  * { box-sizing: border-box; margin: 0; padding: 0; }
  html, body {
    width: 1200px; height: 1059px; overflow: hidden;
    background: var(--backdrop);
    font-family: "Exo 2", sans-serif;
  }
  .canvas { position: relative; width: 1200px; height: 1059px; }

  .card {
    position: absolute;
    width: 640px; height: 366px;
    background: linear-gradient(135deg, var(--card) 0%, var(--card-shade) 100%);
    box-shadow: 0 6px 18px rgba(0,0,0,0.18);
    overflow: hidden;
  }

  /* Front */
  .card-front { left: 500px; top: 90px; }
  .front-brand {
    position: absolute; inset: 0;
    display: flex; align-items: center; justify-content: center; gap: 22px;
  }
  .brand-square { width: 84px; height: 84px; background: var(--teal); }
  .brand-name {
    font-size: 48px; font-weight: 400; color: var(--ink-soft);
    letter-spacing: 1px;
  }

  /* Back */
  .card-back { left: 60px; top: 580px; }
  .back-bands { position: absolute; inset: 0; }
  .back-brand {
    position: absolute; left: 34px; top: 30px;
    display: flex; align-items: center; gap: 10px;
  }
  .back-brand .brand-square { width: 30px; height: 30px; }
  .back-brand .brand-name { font-size: 20px; letter-spacing: 0.5px; }

  .person {
    position: absolute; right: 34px; top: 44px; text-align: right;
    color: var(--teal);
  }
  .person-name { font-size: 25px; font-weight: 600; letter-spacing: 1.5px; text-transform: uppercase; }
  .person-title { font-size: 15px; font-weight: 400; letter-spacing: 2px; text-transform: uppercase; margin-top: 4px; }

  .address {
    position: absolute; right: 34px; top: 222px;
    font-size: 14px; color: var(--ink); letter-spacing: 0.5px;
  }
  .contacts {
    position: absolute; right: 34px; bottom: 22px;
    list-style: none; text-align: right;
  }
  .contacts li {
    display: flex; justify-content: flex-end; align-items: center; gap: 10px;
    font-size: 13.5px; color: var(--ink); letter-spacing: 0.8px;
    line-height: 21px;
  }
  .contacts svg { width: 13px; height: 13px; fill: var(--ink); }
</style>
</head>
<body>
<main class="canvas">

  <section class="card card-front" aria-label="Card front">
    <div class="front-brand">
      <span class="brand-square"></span>
      <span class="brand-name">Velmont Estates</span>
    </div>
  </section>

  <section class="card card-back" aria-label="Card back">
    <svg class="back-bands" viewBox="0 0 640 366" width="640" height="366" aria-hidden="true">
      <polygon fill="var(--band)" points="0,108 250,108 292,150 640,150 640,178 280,178 238,136 0,136"/>
      <polygon fill="var(--band)" points="0,154 228,154 270,196 640,196 640,206 266,206 224,164 0,164" opacity="0"/>
      <polygon fill="var(--band)" points="0,150 232,150 274,192 640,192 640,204 270,204 228,162 0,162"/>
    </svg>

    <div class="back-brand">
      <span class="brand-square"></span>
      <span class="brand-name">Velmont Estates</span>
    </div>

    <div class="person">
      <p class="person-name">Marcus Ellwood</p>
      <p class="person-title">Financial Advisor</p>
    </div>

    <p class="address">27, 9th floor Harbour View Road BKK</p>

    <ul class="contacts">
      <li>081 462 3907
        <svg viewBox="0 0 24 24"><path d="M6.6 10.8a15 15 0 0 0 6.6 6.6l2.2-2.2c.3-.3.7-.4 1-.2 1.1.4 2.3.6 3.6.6.6 0 1 .4 1 1V20c0 .6-.4 1-1 1A17 17 0 0 1 3 4c0-.6.4-1 1-1h3.5c.6 0 1 .4 1 1 0 1.3.2 2.5.6 3.6.1.3 0 .7-.2 1z"/></svg></li>
      <li>081 462 3907
        <svg viewBox="0 0 24 24"><path d="M7 1h10a2 2 0 0 1 2 2v18a2 2 0 0 1-2 2H7a2 2 0 0 1-2-2V3a2 2 0 0 1 2-2zm0 3v14h10V4zm5 15.5a1 1 0 1 0 0 2 1 1 0 0 0 0-2z"/></svg></li>
      <li>081 462 3907
        <svg viewBox="0 0 24 24"><path d="M6 2h9l3 3v5H6zM3 11h18v10H3zm3 3v2h4v-2zm7 0v2h5v-2z"/></svg></li>
      <li>marcus@velmontestates.asia
        <svg viewBox="0 0 24 24"><path d="M2 5h20v14H2zm2 2v.5l8 5 8-5V7zm0 3v7h16v-7l-8 5z"/></svg></li>
      <li>www.velmontestates.com
        <svg viewBox="0 0 24 24"><path d="M12 2a10 10 0 1 0 0 20 10 10 0 0 0 0-20zm6.9 6h-3a15 15 0 0 0-1.3-3.9A8 8 0 0 1 18.9 8zM12 4c.8 1.2 1.5 2.5 1.9 4h-3.8c.4-1.5 1.1-2.8 1.9-4zM4.3 14a8 8 0 0 1 0-4h3.4a16 16 0 0 0 0 4zm.8 2h3a15 15 0 0 0 1.3 3.9A8 8 0 0 1 5.1 16zm3-8h-3a8 8 0 0 1 4.3-3.9C8.8 5.3 8.4 6.6 8.1 8zM12 20c-.8-1.2-1.5-2.5-1.9-4h3.8c-.4 1.5-1.1 2.8-1.9 4zm2.3-6H9.7a14 14 0 0 1 0-4h4.6a14 14 0 0 1 0 4zm.3 5.9c.6-1.2 1-2.5 1.3-3.9h3a8 8 0 0 1-4.3 3.9zm1.7-5.9a16 16 0 0 0 0-4h3.4a8 8 0 0 1 0 4z"/></svg></li>
    </ul>
  </section>

</main>
</body>
</html>
```